Hop Bright Meadow Business Website Branding

Looking for a wordpress template design with CSS and HTML encoding. Current website can be seen at hopbrightmeadow.example.

WE ARE CURRENTLY IN PROCESS GETTING A LOGO DESIGN... I HAVE INCLUDED THE TOP POTENTIAL DESIGNS FOR REFERENCE TO HELP UNDERSTAND WHAT STYLE WE ARE LOOKING FOR...
NOTE: THE “PEBBLE CREW” LOGO WAS A PREVIOUS COMPANY WE OWNED SO YOU CAN GE A FEEL FOR THE TYPE OF DESIGNS WE HAVE USED IN THE PAST.

My blog will focus on making a connection with wild Florida, it’s wildlife, plants and animals... with an eye toward Florida conservation, nature adventure trips, and education... Content, photos and other merchandise will also be offered for sale.
I’m looking for a site design that incorporates Florida nature and wildlife/plants, with a fun “Old Florida” retro-adventure feel.
When they see this site it should speak to the import of natural Florida and the critical nature of the ecosystem here... while being instantly recognizable and iconic... IE: when I think of florida I think of water, plants, warmth, sunsets etc...

https://join.chatroomhub.example/t/lumexstudio-kzt4821/shared_invite/zt-pqwrt83m-hRnLvXaKoPzsYcB1Uq7JdM

Target Market(s)

Nature, Education, Conservation, Photography

Industry/Entity Type

Photographer

Coding

Coded - Design and coding required

Requirements
Must have
• Need to have site wide template design which generally includes a landing page and a general page template for other pages... Must include html and css encoding...
Should not have
• Any animals included in the site should be Florida native... IE: no African animals etc... This will require some research to ensure that if animals are included that they are part of the Florida ecosystem.

```html
<!DOCTYPE html>
<html lang="en">
<head>
<meta charset="utf-8">
<title>Hop Bright Meadow</title>
<link href="https://fonts.googleapis.com/css2?family=Alfa+Slab+One&family=Roboto:wght@400;500;700&family=Baloo+2:wght@600&display=swap" rel="stylesheet">
<style>
:root{
  --parch-light:#a08e6a;
  --parch-mid:#8a7552;
  --parch-dark:#5c4a30;
  --ink:#000000;
  --white:#ffffff;
  --navy:#1c2a44;
  --navy-deep:#0f1a2e;
  --footer:#000000;
  --muted:#e8e2d6;
  --social:#2f4d9c;
}
*{margin:0;padding:0;box-sizing:border-box}
html,body{width:1200px;height:3844px;overflow:hidden}
body{position:relative;font-family:"Roboto",sans-serif;color:var(--white);
  background:radial-gradient(ellipse at 50% 30%,var(--parch-light),var(--parch-mid) 55%,var(--parch-dark));}
.abs{position:absolute}
.slab{font-family:"Alfa Slab One",serif;font-weight:400;letter-spacing:1px}

/* header + hero */
.hero{left:0;top:0;width:1200px;height:730px;
  background:linear-gradient(180deg,#3d4a1e 0%,#2c3416 35%,#3b2e16 70%,#5a4622 100%)}
.site-header{left:0;top:0;width:1200px;height:82px;background:rgba(60,48,28,.75)}
.brand{left:88px;top:14px;font-family:"Baloo 2",sans-serif;font-weight:600;font-size:46px;line-height:1;color:var(--white)}
.nav{top:32px;right:84px;display:flex;gap:40px;font-size:17px}
.nav a{color:var(--white);text-decoration:none}
.nav a.current{color:#111}
.hero-title{left:0;top:130px;width:1200px;text-align:center;font-size:50px;line-height:60px;color:var(--white)}
.hero-wave{left:0;top:640px}

/* welcome */
.circle-frame{border-radius:50%;background:var(--ink)}
.circle-photo{border-radius:50%}
.welcome-title{left:641px;top:930px;font-size:40px;line-height:42px;color:var(--white)}
.welcome-text{left:641px;top:1042px;width:466px;font-size:15.5px;line-height:33px;text-align:justify}

/* nature band */
.nature{left:0;top:1470px;width:1200px;height:646px;
  background:radial-gradient(ellipse at 50% 20%,#24365a,var(--navy) 50%,var(--navy-deep))}
.nature-title{left:0;top:1580px;width:1200px;text-align:center;font-size:40px}

/* about */
.about-title{left:90px;top:2282px;font-size:40px;color:var(--white)}
.about-text{left:90px;top:2348px;width:466px;font-size:16px;line-height:33.3px;text-align:justify}
.about-text b{font-weight:700}

/* blog */
.blog-title{left:0;top:2852px;width:1200px;text-align:center;font-size:40px}
.card{top:2913px;width:336px}
.card-img{width:336px;height:226px}
.card h3{margin-top:18px;font-size:16px;line-height:23px;font-weight:700}
.card .date{margin-top:12px;font-size:14px;color:var(--muted)}
.card .more{margin-top:14px;font-size:16px;font-weight:700;display:block}
.arrow{top:3015px;font-size:22px;font-weight:700}

/* footer */
.footer{left:0;top:3380px;width:1200px;height:464px}
.f-head{font-size:21px;font-weight:700}
.f-small{font-size:13px;line-height:18px}
.f-links{font-size:13px;line-height:27px}
.divider{width:1px;height:186px;background:#444;top:3560px}
.news-input{left:830px;top:3654px;width:243px;height:38px;background:var(--white);color:#999;font-size:11px;padding:12px 14px}
.news-btn{left:1073px;top:3654px;width:40px;height:38px;background:#222;display:flex;align-items:center;justify-content:center}
.social{top:3723px;left:830px;display:flex;gap:14px}
.social span{width:32px;height:32px;border-radius:50%;background:var(--social);display:block}
.copy{left:0;top:3802px;width:1200px;text-align:center;font-size:11px}
</style>
</head>
<body>

<div class="abs hero" role="img" aria-label="Two roseate spoonbills facing each other with wings raised in shallow dark water"></div>
<header class="abs site-header"></header>
<div class="abs brand">Hop Bright Meadow</div>
<nav class="abs nav">
  <a class="current" href="#">Home</a><a href="#">About Us</a><a href="#">Blog</a><a href="#">Gallery</a><a href="#">Contact Us</a>
</nav>
<h1 class="abs hero-title slab">FLORIDA MASTER NATURALIST<br>UPLANDS NATURE</h1>
<svg class="abs hero-wave" width="1200" height="100" viewBox="0 0 1200 100">
  <path d="M0 20 C150 10 350 30 520 12 C600 4 620 90 700 70 C800 40 1000 20 1200 15 L1200 100 L0 100 Z" fill="#8e7a55"/>
</svg>

<!-- welcome -->
<div class="abs circle-frame" style="left:90px;top:846px;width:506px;height:504px"></div>
<div class="abs circle-photo" style="left:100px;top:848px;width:496px;height:496px;background:radial-gradient(circle at 45% 45%,#8a6a3a,#5e4a22 60%,#3c3a1a)" role="img" aria-label="Red wolf in profile against a warm blurred background"></div>
<h2 class="abs welcome-title slab">WELCOME TO<br>HOP BRIGHT MEADOW</h2>
<p class="abs welcome-text">Come explore wild places and stunning scenery with me as I discover new and exciting eco-adventures and learn about the rare and unique wildlife and environments that make Florida so precious and extraordinary. I hope you can vicariously enjoy the wild and untamed beauty of Florida through my eyes, and learn some amazing things about nature on our explorations.</p>

<!-- nature -->
<section class="abs nature" role="img" aria-label="Underwater coral reef with tropical fish"></section>
<h2 class="abs nature-title slab">OUR NATURE</h2>
<div class="abs circle-photo" style="left:77px;top:1656px;width:338px;height:338px;background:radial-gradient(circle,#c7b4d6,#5a8a2a 45%,#2f5a18)" role="img" aria-label="Pale purple wildflower among green leaves"></div>
<div class="abs circle-photo" style="left:430px;top:1656px;width:338px;height:338px;background:radial-gradient(circle at 45% 40%,#f06a4a,#d8b8a8 70%,#b8a090)" role="img" aria-label="American flamingo preening"></div>
<div class="abs circle-photo" style="left:782px;top:1656px;width:338px;height:338px;background:linear-gradient(180deg,#5a7030,#b08a5a 45%,#5a9a2a)" role="img" aria-label="Florida panther on green grass"></div>

<!-- about -->
<h2 class="abs about-title slab">ABOUT US</h2>
<p class="abs about-text">Hello nature lovers! I'm Marisol Tennant, a wildlife educator, Florida Master Naturalist, nature writer and photographer, busy mama of three kiddos, a playful Havanese puppy, two very chubby guinea pigs, and a giant tree frog. I have a passion for all things nature and I adore living in Southwest Florida. I will always be a California girl, but from the moment I set foot in Florida, its wild beauty stole my heart. For the past 23 years, I have been fortunate to have some very unique and special experiences caring for many different species of animals and educating the public about wildlife and the environment...<b>Read More</b></p>
<div class="abs circle-frame" style="left:605px;top:2234px;width:506px;height:504px"></div>
<div class="abs circle-photo" style="left:605px;top:2236px;width:496px;height:496px;background:radial-gradient(circle,#f5a62a,#e07a18 45%,#4a7a22)" role="img" aria-label="Two orange and black butterflies on orange blossoms"></div>

<!-- blog -->
<h2 class="abs blog-title slab">BLOG</h2>
<span class="abs arrow" style="left:38px">&#8249;</span>
<span class="abs arrow" style="left:1150px">&#8250;</span>
<article class="abs card" style="left:90px">
  <div class="card-img" style="background:linear-gradient(135deg,#4a6a22,#c8b0e0 50%,#3a5a1a)" role="img" aria-label="Lavender wildflower in grass"></div>
  <h3>Communing with Nature at Saw Creek Cypress Dome Preserve Trails</h3>
  <p class="date">September 24th-October 22nd, 2020</p>
  <a class="more">Read More</a>
</article>
<article class="abs card" style="left:433px">
  <div class="card-img" style="background:radial-gradient(circle at 55% 45%,#f2d41a,#5a8a2a 35%,#2e5218)" role="img" aria-label="Yellow flower among green foliage"></div>
  <h3>Environmental Ethics Statement</h3>
  <p class="date">September 24th-October 22nd, 2020</p>
  <a class="more">Read More</a>
</article>
<article class="abs card" style="left:776px">
  <div class="card-img" style="background:radial-gradient(circle at 50% 50%,#e8d42a,#6a9a3a 40%,#3a6a22)" role="img" aria-label="Yellow blossoms on a green shrub"></div>
  <h3>Saw Creek Cypress Dome Trails</h3>
  <p class="date">September 24th-October 22nd, 2020</p>
  <a class="more">Read More</a>
</article>

<!-- footer -->
<svg class="abs" style="left:0;top:3380px" width="1200" height="464" viewBox="0 0 1200 464">
  <path d="M0 70 C200 70 420 66 500 50 C540 30 560 8 590 12 C640 20 700 55 760 60 C900 65 1050 45 1200 60 L1200 464 L0 464 Z" fill="#000"/>
</svg>
<h4 class="abs f-head" style="left:90px;top:3544px">Contact Us</h4>
<p class="abs f-small" style="left:90px;top:3591px">Company<br>14 Heron Lane. Cedar Point,Florida</p>
<p class="abs f-small" style="left:87px;top:3650px">Email address<br>info@hopbrightmeadow.example</p>
<p class="abs f-small" style="left:89px;top:3709px">Call us<br>0100-22 33 44</p>
<div class="abs divider" style="left:370px"></div>
<h4 class="abs f-head" style="left:422px;top:3544px">Links</h4>
<p class="abs f-links" style="left:424px;top:3590px">Home<br>About Us<br>Blog<br>Gallery<br>Contact Us</p>
<div class="abs divider" style="left:580px"></div>
<p class="abs f-links" style="left:625px;top:3590px">Privacy Policy<br>Terms &amp; Conditions<br>FAQ<br>Sitemap</p>
<div class="abs divider" style="left:766px"></div>
<h4 class="abs f-head" style="left:828px;top:3544px">Newsletter</h4>
<p class="abs f-small" style="left:830px;top:3596px;width:270px">For exclusive news and updates sign up for our newsletter.</p>
<div class="abs news-input">Email Address</div>
<div class="abs news-btn"><svg width="16" height="16" viewBox="0 0 16 16"><path d="M1 7 L15 1 L10 15 L7 9 Z M7 9 L15 1" fill="none" stroke="#fff" stroke-width="1.3"/></svg></div>
<div class="abs social"><span></span><span></span><span></span><span></span><span></span></div>
<p class="abs copy">© 2020 Copyrights.THE COMPANY NAME.All Rights Reserved</p>

</body>
</html>
```